BVL - New Homepage needed for an existing website

Bright Valley Lantern Website
Need a new Homepage for an existing website with Action Items and Newer Pictures
This is the current Website
https://brightvalleylantern.example/

This new page will be changed on Jan 21st when Voting begins
1. Voting like a political campaign where we are trying to raise awareness for the issues we stand for and urge the people to go to a Polling /voting website and vote for us (Roster 4)
2. We have 6 basic themes as to what we stand for - there will be text to promote their importance of voting/call to action
3. There will be videos on the website and there will be a simulation of how the voting process works - will be added later

Use colors like the US Flag - Red, White and Blue. The other pages don't need to be changed - only the HomePage.

I only need the design, I will code the website. Thank you

Target Market(s)

Jewish People in the US

Industry/Entity Type

Religious

Number of Pages Required

1 page

Font styles to use
Serif
Sans Serif

Colors

Designer to choose colors to be used in the design.

Requirements
Must have
• Call to Action - Go out to Vote
• This is the current Website - https://brightvalleylantern.example/

```html
<!DOCTYPE html>
<html lang="en">
<head>
<meta charset="utf-8">
<title>Bright Valley Lantern — Home</title>
<link rel="stylesheet" href="https://fonts.googleapis.com/css2?family=Montserrat:wght@300;400;500;600;700&display=swap">
<style>
:root{
  --navy:#221a5c;
  --navy-deep:#1b1450;
  --brown:#8a3516;
  --brown-dark:#7a2c10;
  --white:#ffffff;
  --ink:#2a2a2a;
  --muted:#555555;
  --soft:#f3f3f5;
}
*{margin:0;padding:0;box-sizing:border-box}
html,body{width:1200px;height:3837px;overflow:hidden}
body{position:relative;font-family:'Montserrat',sans-serif;color:var(--ink);background:var(--white)}
a{color:inherit;text-decoration:none}
.abs{position:absolute}

/* hero */
.hero{position:absolute;left:0;top:0;width:1200px;height:740px}
.hero-art{position:absolute;inset:0}
.brand{position:absolute;left:109px;top:48px;display:flex;align-items:center;gap:10px;color:var(--white);font-weight:700;font-size:26px;letter-spacing:1px}
.brand-box{width:22px;height:22px;background:var(--white)}
.phone{position:absolute;left:930px;top:18px;color:var(--white);font-size:15px;font-weight:600;display:flex;gap:8px;align-items:center}
.main-nav{position:absolute;top:58px;left:555px;font-size:15px;color:var(--white)}
.main-nav a{position:absolute;white-space:nowrap}
.main-nav .on{text-decoration:underline}
.hero-title{position:absolute;left:110px;top:272px;color:var(--white);font-size:52px;font-weight:700;letter-spacing:.5px;white-space:nowrap}
.hero-sub{position:absolute;left:109px;top:350px;width:740px;color:var(--white);font-size:26px;line-height:38px;font-weight:400}
.btn{position:absolute;display:flex;align-items:center;gap:18px;padding-left:24px;height:46px;width:238px;color:var(--white);font-size:18px;font-weight:500}
.btn svg{width:34px;height:30px}
.btn-hero{left:112px;top:467px;background:rgba(30,22,70,.55)}
.dots{position:absolute;display:flex;align-items:center;gap:16px}
.dot{width:10px;height:12px;border:1.5px solid var(--white)}
.dot.big{width:24px;height:24px;border-radius:50%;background:var(--white);border:none}

/* about */
.eyebrow{left:116px;top:861px;font-size:15px;color:var(--brown)}
.about-title{left:113px;top:898px;font-size:44px;font-weight:700;color:var(--brown)}
.about-text{left:110px;top:974px;width:492px;font-size:15px;line-height:32px;text-align:justify}
.btn-brown{left:112px;top:1203px;background:var(--brown);box-shadow:0 6px 12px rgba(0,0,0,.2)}
.about-art{left:692px;top:864px;width:341px;height:394px;background:linear-gradient(150deg,#9a9a9a,#2a2a2a)}

/* services */
.section-title{left:0;width:1200px;text-align:center;font-weight:700}
.services-title{top:1404px;font-size:42px;color:var(--navy)}
.card{position:absolute;width:252px;height:234px;background:var(--white);box-shadow:0 2px 14px rgba(0,0,0,.09);text-align:center}
.card.active{border:1px solid #d9d6e6}
.card svg{position:absolute;left:102px;top:26px;width:48px;height:48px}
.card h3{position:absolute;top:96px;width:100%;font-size:14px;font-weight:500;color:#111;white-space:nowrap}
.card p{position:absolute;top:125px;left:22px;width:208px;font-size:10px;line-height:17px;color:var(--muted);text-align:center}
.card a{position:absolute;top:190px;left:0;width:100%;font-size:13px;text-decoration:underline;color:#222}

/* mission */
.mission{left:0;top:2141px;width:1200px;height:669px;background:var(--soft)}
.mission-frame{left:82px;top:2229px;width:593px;height:508px;border:2px solid var(--navy)}
.mission-photo{left:112px;top:2213px;width:580px;height:491px;background:linear-gradient(135deg,#3d2f7a,#2a1f63 60%,#4a3a8a)}
.mission-card{left:543px;top:2275px;width:569px;height:377px;background:var(--white);box-shadow:0 4px 20px rgba(0,0,0,.06)}
.mission-card h2{position:absolute;left:53px;top:48px;font-size:34px;font-weight:700;color:var(--navy);white-space:nowrap}
.mission-card h4{position:absolute;left:53px;top:104px;font-size:26px;font-weight:300;color:var(--navy)}
.mission-card p{position:absolute;left:53px;top:152px;width:480px;font-size:15.5px;line-height:30px;text-align:justify}
.btn-navy{left:600px;top:2558px;background:var(--navy);box-shadow:0 6px 12px rgba(0,0,0,.2)}

/* news */
.news-title{top:2890px;font-size:36px;color:var(--brown)}
.news-sub{left:0;top:2948px;width:1200px;text-align:center;font-size:17px;line-height:25px}
.news-card{position:absolute;width:283px;height:374px}
.news-img{position:absolute;left:0;top:0;width:283px;height:190px;border-radius:8px 8px 0 0;background:linear-gradient(160deg,#d8d8d8,#5a5a5a)}
.news-body{position:absolute;left:6px;top:180px;width:271px;height:194px;background:var(--white);border-top:3px solid var(--brown);border-bottom:4px solid var(--brown);box-shadow:0 2px 10px rgba(0,0,0,.08);text-align:center}
.meta{position:absolute;top:24px;width:100%;font-size:9px;display:flex;justify-content:center;align-items:center;gap:6px}
.meta i{display:inline-block;width:9px;height:9px;border-radius:50%;background:var(--brown)}
.news-body h3{position:absolute;top:50px;left:20px;width:231px;font-size:13.5px;line-height:19px;font-weight:600;color:#111}
.news-body p{position:absolute;top:100px;left:30px;width:211px;font-size:10px;line-height:18px;color:var(--ink)}
.news-body a{position:absolute;top:153px;left:0;width:100%;font-size:13px;color:var(--brown);text-decoration:underline}
.dot-b{border-color:var(--brown)}
.dot-b.big{background:var(--brown)}

/* footer */
.footer-band{left:0;top:3590px;width:1200px;height:247px}
.footer-mark{left:326px;top:3545px;width:116px;height:116px;border-radius:50%;background:var(--white);display:flex;align-items:center;justify-content:center;gap:6px;font-weight:700;font-size:22px;color:var(--brown)}
.footer-mark span.sq{width:12px;height:12px;background:var(--brown)}
.footer-nav{top:3698px;color:var(--white);font-size:15px}
.footer-nav a{position:absolute;white-space:nowrap}
.copy{left:0;top:3746px;width:1200px;text-align:center;color:var(--white);font-size:13px}
.social{position:absolute;top:3794px;width:22px;height:22px;background:var(--brown)}
</style>
</head>
<body>

<header class="hero">
  <svg class="hero-art" width="1200" height="740" viewBox="0 0 1200 740">
    <defs>
      <linearGradient id="flag" x1="0" y1="0" x2="1" y2="0.4">
        <stop offset="0" stop-color="#2c2278"/>
        <stop offset=".45" stop-color="#4a3590"/>
        <stop offset=".7" stop-color="#9a2440"/>
        <stop offset="1" stop-color="#c8d0de"/>
      </linearGradient>
    </defs>
    <polygon role="img" aria-label="Waving national flag photograph" points="0,0 1200,0 1200,618 365,728 0,585" fill="url(#flag)"/>
    <polygon points="0,585 365,728 1200,618 1200,628 365,740 0,597" fill="#8a3516"/>
  </svg>
  <div class="brand"><span class="brand-box"></span>BVL</div>
  <div class="phone">
    <svg width="14" height="14" viewBox="0 0 24 24"><rect width="24" height="24" rx="4" fill="#fff"/><path d="M7 5l3 3-2 2c1 2 3 4 5 5l2-2 3 3-2 3C10 19 5 14 5 7z" fill="#2c2278"/></svg>
    (555) 014-2288
  </div>
  <nav class="main-nav">
    <a class="on" style="left:0">HOME</a>
    <a style="left:87px">ABOUT US</a>
    <a style="left:206px">SERVICES</a>
    <a style="left:319px">NEWS</a>
    <a style="left:405px">CONTACT US</a>
  </nav>
  <h1 class="hero-title">BRIGHT VALLEY LANTERN</h1>
  <p class="hero-sub">Lorem ipsum dolor sit amet, consectetur adipiscing elit, sed do eiusmod tempor incididunt ut labore</p>
  <a class="btn btn-hero">READ MORE
    <svg viewBox="0 0 34 30"><path d="M17 2L32 28H2z" fill="none" stroke="#fff" stroke-width="3"/></svg>
  </a>
  <div class="dots" style="left:548px;top:636px">
    <span class="dot"></span><span class="dot big"></span><span class="dot"></span><span class="dot"></span>
  </div>
</header>

<section>
  <p class="abs eyebrow">WELCOME BRIGHT VALLEY LANTERN</p>
  <h2 class="abs about-title">ABOUT US</h2>
  <p class="abs about-text">Lorem ipsum dolor sit amet, consectetur adipiscing elit, sed do eiusmod tempor incididunt ut labore et dolore magna aliqua. Quis ipsum suspendisse ultrices gravida. Risus commodo viverra maecenas accumsan lacus vel facilisis. Lorem ipsum dolor sit amet, consectetur adipiscing elit, sed do eiusmod tempor incididunt ut labore et dolore magna aliqua.</p>
  <a class="btn btn-brown">READ MORE
    <svg viewBox="0 0 34 30"><path d="M17 2L32 28H2z" fill="none" stroke="#fff" stroke-width="3"/></svg>
  </a>
  <div class="abs about-art" role="img" aria-label="Six-pointed star artwork with monochrome photograph inside"></div>
</section>

<section>
  <h2 class="abs section-title services-title">OUR SERVICES</h2>

  <div class="card" style="left:202px;top:1523px">
    <svg viewBox="0 0 48 48"><circle cx="24" cy="24" r="22" fill="#221a5c"/></svg>
    <h3>Resist Assimilation</h3>
    <p>Assimilation is an issue facing every religion. With respect to Judaism, Bright Valley Lantern underscores</p>
    <a>DISCOVER MORE</a>
  </div>
  <div class="card active" style="left:475px;top:1523px">
    <svg viewBox="0 0 48 48"><path d="M24 3L44 37H4zM24 45L4 11H44z" fill="none" stroke="#221a5c" stroke-width="2.5"/></svg>
    <h3>Confront Anti-Semitism</h3>
    <p>Anti-Semitism in America is unfortunately becoming the new norm. While the attacks against</p>
    <a>DISCOVER MORE</a>
  </div>
  <div class="card" style="left:746px;top:1523px">
    <svg viewBox="0 0 48 48"><rect x="6" y="12" width="36" height="26" fill="#221a5c"/></svg>
    <h3>Expose Boycott Efforts</h3>
    <p>Boycott efforts have not yet gained enough traction to be a real threat, but the threat of boycotts looms</p>
    <a>DISCOVER MORE</a>
  </div>
  <div class="card" style="left:202px;top:1779px">
    <svg viewBox="0 0 48 48"><rect x="10" y="4" width="28" height="40" rx="2" fill="#221a5c"/><path d="M24 16l6 10H18zM24 32l-6-10h12z" fill="none" stroke="#fff" stroke-width="1.5"/></svg>
    <h3>Instill Jewish Pride</h3>
    <p>Due to the atmosphere on many if not most of our American college campuses, students are ashamed</p>
    <a>DISCOVER MORE</a>
  </div>
  <div class="card" style="left:475px;top:1779px">
    <svg viewBox="0 0 48 48" style="left:82px;width:88px"><path d="M1 44L16 16l8 12 8-22 15 38z" fill="none" stroke="#221a5c" stroke-width="2.5" stroke-linejoin="round"/></svg>
    <h3>Eternal Jewish Homeland</h3>
    <p>For thousands of years, Judaism has been inextricably bound with Israel. Since 1948, Israel has been</p>
    <a>DISCOVER MORE</a>
  </div>
  <div class="card" style="left:746px;top:1779px">
    <svg viewBox="0 0 48 48"><path d="M24 3L44 37H4zM24 45L4 11H44z" fill="none" stroke="#221a5c" stroke-width="4"/></svg>
    <h3>Maintain Israel's Jewish Identity</h3>
    <p>While we recognize that Jews are empowered with free choice, particularly in their beliefs</p>
    <a>DISCOVER MORE</a>
  </div>
</section>

<section>
  <div class="abs mission"></div>
  <div class="abs mission-frame"></div>
  <div class="abs mission-photo" role="img" aria-label="Portrait photograph of a smiling woman on a purple background"></div>
  <div class="abs mission-card">
    <h2>BRIGHT VALLEY LANTERN</h2>
    <h4>MISSION STATEMENT</h4>
    <p>Bright Valley Lantern is a grassroots movement that was established to promote Jewish Continuity, recognizing that in the United States, Judaism and its continuity</p>
  </div>
  <a class="btn btn-navy">READ MORE
    <svg viewBox="0 0 34 30"><path d="M17 2L32 28H2z" fill="none" stroke="#fff" stroke-width="3"/></svg>
  </a>
</section>

<section>
  <h2 class="abs section-title news-title">NEWS</h2>
  <p class="abs news-sub">Lorem ipsum dolor sit amet, consectetur adipi-<br>scing elit, sed do eiusmod</p>

  <article class="news-card" style="left:113px;top:3051px">
    <div class="news-img" role="img" aria-label="Monochrome photograph of hands resting on a book"></div>
    <div class="news-body">
      <div class="meta">BY ADMIN &nbsp;|&nbsp; <i></i> 05 march 2019</div>
      <h3>LOREM IPSUM DOLOR SIT AMET, CONSECTETUR ADIPI-</h3>
      <p>Lorem ipsum dolor sit amet, consectetur adipiscing elit, sed do eiusmod</p>
      <a>DISCOVER MORE</a>
    </div>
  </article>
  <article class="news-card" style="left:459px;top:3051px">
    <div class="news-img" role="img" aria-label="Monochrome photograph of a wedding ring ceremony"></div>
    <div class="news-body">
      <div class="meta">BY ADMIN &nbsp;|&nbsp; <i></i> 05 march 2019</div>
      <h3>LOREM IPSUM DOLOR SIT AMET, CONSECTETUR ADIPI-</h3>
      <p>Lorem ipsum dolor sit amet, consectetur adipiscing elit, sed do eiusmod</p>
      <a>DISCOVER MORE</a>
    </div>
  </article>
  <article class="news-card" style="left:806px;top:3051px">
    <div class="news-img" role="img" aria-label="Monochrome photograph of stones placed on a memorial stone" style="background:linear-gradient(160deg,#8a8a8a,#2e2e2e)"></div>
    <div class="news-body">
      <div class="meta">BY ADMIN &nbsp;|&nbsp; <i></i> 05 march 2019</div>
      <h3>LOREM IPSUM DOLOR SIT AMET, CONSECTETUR ADIPI-</h3>
      <p>Lorem ipsum dolor sit amet, consectetur adipiscing elit, sed do eiusmod</p>
      <a>DISCOVER MORE</a>
    </div>
  </article>

  <div class="dots" style="left:566px;top:3468px;gap:12px">
    <span class="dot dot-b"></span><span class="dot dot-b"></span><span class="dot dot-b big" style="width:20px;height:20px"></span><span class="dot dot-b"></span>
  </div>
</section>

<footer>
  <svg class="abs footer-band" width="1200" height="247" viewBox="0 0 1200 247">
    <polygon role="img" aria-label="Dark blue photograph of a congregation" points="0,70 1200,12 1200,247 0,247" fill="#2c237a"/>
  </svg>
  <div class="abs footer-mark"><span class="sq"></span>BVL</div>
  <nav class="abs footer-nav">
    <a style="left:347px">HOME</a>
    <a style="left:433px">ABOUT US</a>
    <a style="left:552px">SERVICES</a>
    <a style="left:666px">NEWS</a>
    <a style="left:752px">CONTACT US</a>
  </nav>
  <p class="abs copy">© Copyrights Bright Valley Lantern 2020.All rights reserved</p>
  <span class="social" style="left:485px"></span>
  <span class="social" style="left:558px"></span>
  <span class="social" style="left:631px"></span>
</footer>

</body>
</html>
```